Pop up exhibition stand 2000mm (H) x 800mm (W)

I would like a simple pop up banner stand for an exhibition.

We need a pop up banner stand design for 'Brisk Forge Processing'

the size is 2000mm(H) x 800mm (W)

Ad copy as follows :

[Brisk Forge logo]

From Sheet Metal To Large Sand Castings

Our Capacity and Rapid Quenching drop bottom ovens deliver precise processing.
We also serve the leading names in aerospace, automotive and advanced engineering.

Visit www.briskforge.example/ or call us Tel: +44 (0)1632 960418

[Put the crafted by the vale logo here, also include the text member somewhere close]

check on their website for other ideas that can help you with this project.

Target Market(s)

will be used at a trade show

Requirements
Nice to have
• modern design for UK manufacturing business

```html
<!DOCTYPE html>
<html lang="en">
<head>
<meta charset="utf-8">
<title>Brisk Forge Processing – Exhibition Stand</title>
<link rel="stylesheet" href="https://fonts.googleapis.com/css2?family=Nunito:wght@400;600;700;800&display=swap">
<style>
  :root {
    --orange: #f26a21;
    --orange-light: #f79a3a;
    --red: #e2342b;
    --ink: #58595b;
    --panel: #8c8f93;
    --white: #ffffff;
    --rule: #b8babd;
  }
  * { margin: 0; padding: 0; box-sizing: border-box; }
  html, body { width: 1200px; height: 2984px; overflow: hidden; background: var(--white); }
  body { font-family: "Nunito", Arial, sans-serif; color: var(--ink); }
  .stand { position: relative; width: 1200px; height: 2984px; overflow: hidden; background: var(--white); }

  .top-band { position: absolute; top: 0; left: 0; width: 100%; height: 40px;
    background: linear-gradient(90deg, var(--orange-light), var(--orange)); }

  .brand { position: absolute; top: 110px; left: 110px; display: flex; align-items: center; gap: 28px; }
  .brand-dot { width: 120px; height: 120px; border-radius: 50%; background: var(--orange); }
  .brand-name { font-size: 90px; font-weight: 800; color: var(--orange); line-height: 1; }
  .brand-tagline { position: absolute; top: 245px; left: 258px; font-size: 50px; font-weight: 600;
    color: var(--red); line-height: 1.15; }

  .headline { position: absolute; top: 405px; left: 0; width: 100%; text-align: center;
    font-weight: 700; line-height: 1.12; }
  .headline .small { color: var(--ink); font-size: 80px; }
  .headline .big { color: var(--red); font-size: 108px; }

  .photo { position: absolute; top: 660px; left: 0; width: 100%; height: 1120px;
    background:
      radial-gradient(ellipse 420px 620px at 260px 620px, rgba(255,255,255,0.85), rgba(255,255,255,0) 70%),
      radial-gradient(ellipse 120px 380px at 300px 820px, rgba(200,40,40,0.55), rgba(200,40,40,0) 75%),
      radial-gradient(ellipse 520px 360px at 880px 820px, rgba(225,228,232,0.9), rgba(225,228,232,0) 75%),
      linear-gradient(180deg, #3f4247 0%, #6b6f75 30%, #a4a8ad 62%, #d3d6d9 100%); }

  .swoosh { position: absolute; top: 1300px; left: 0; width: 1200px; height: 480px; display: block; }
  .panel { position: absolute; top: 1778px; left: 0; width: 100%; height: 622px; background: var(--panel); }

  .sectors { position: absolute; top: 1850px; left: 0; width: 100%; display: flex; justify-content: space-around;
    padding: 0 40px; }
  .sector { display: flex; flex-direction: column; align-items: center; gap: 14px; width: 300px; }
  .sector svg { height: 100px; width: 160px; }
  .sector-label { font-size: 28px; font-weight: 700; color: var(--red); letter-spacing: 1px; }

  .pitch { position: absolute; top: 2035px; left: 70px; width: 1070px; color: var(--white);
    font-size: 43px; font-weight: 400; line-height: 1.62; }
  .pitch strong { font-weight: 800; }

  .contact { position: absolute; top: 2435px; left: 0; width: 100%; display: flex; justify-content: center;
    align-items: center; gap: 34px; font-size: 42px; font-weight: 600; color: var(--ink); }
  .contact-item { display: flex; align-items: center; gap: 14px; }
  .contact-item svg { width: 38px; height: 38px; }
  .divider { width: 4px; height: 90px; background: var(--rule); }

  .membership { position: absolute; top: 2555px; left: 0; width: 100%; display: flex; justify-content: center;
    align-items: center; gap: 40px; }
  .member-label { font-size: 40px; font-weight: 600; color: var(--ink); }
  .membership .divider { height: 160px; }
  .partner { display: flex; align-items: center; gap: 26px; }
  .partner-badge { width: 160px; height: 160px; border-radius: 50%; background: #e5e6e7; border: 8px solid #a3a5a8; }
  .partner-name { font-size: 48px; font-weight: 700; color: var(--red); line-height: 1.05; text-transform: uppercase; }

  .bottom-band { position: absolute; bottom: 0; left: 0; width: 100%; height: 240px;
    background: linear-gradient(90deg, var(--orange), var(--red)); }
</style>
</head>
<body>
<div class="stand">
  <div class="top-band"></div>

  <div class="brand">
    <div class="brand-dot"></div>
    <div class="brand-name">Brisk Forge</div>
  </div>
  <div class="brand-tagline">the solution in<br>aluminium heat treatment</div>

  <h1 class="headline">
    <span class="small">From </span><span class="big">Sheet Metal</span><span class="small"> To</span><br>
    <span class="big">Large Sand Castings</span>
  </h1>

  <div class="photo" role="img" aria-label="Company representative in a white shirt and red tie standing in a heat treatment workshop beside machined aluminium blocks"></div>

  <svg class="swoosh" viewBox="0 0 1200 480" preserveAspectRatio="none" aria-hidden="true">
    <defs>
      <linearGradient id="swooshFill" x1="0" y1="0" x2="1" y2="0">
        <stop offset="0" stop-color="#f26a21"/>
        <stop offset="1" stop-color="#e2342b"/>
      </linearGradient>
    </defs>
    <path d="M0 400 C450 385 880 190 1200 0 L1200 60 C900 230 420 430 0 440 Z" fill="url(#swooshFill)"/>
    <path d="M0 440 C420 430 900 230 1200 60 L1200 480 L0 480 Z" fill="#8c8f93"/>
  </svg>
  <div class="panel"></div>

  <div class="sectors">
    <div class="sector">
      <svg viewBox="0 0 160 100" aria-hidden="true">
        <path d="M10 62 L140 30 Q156 28 150 40 L34 76 Z M60 52 L40 20 L56 18 L92 44 Z M60 62 L66 92 L80 90 L86 58 Z M14 64 L6 44 L16 44 L28 58 Z" fill="#fff"/>
      </svg>
      <span class="sector-label">AEROSPACE</span>
    </div>
    <div class="sector">
      <svg viewBox="0 0 160 100" aria-hidden="true">
        <path d="M14 72 L14 52 Q16 44 30 42 L46 22 Q52 16 64 16 L104 16 Q116 16 124 26 L138 42 Q148 46 148 56 L148 72 Z" fill="#fff"/>
        <path d="M54 24 L66 24 L66 40 L40 40 Z M74 24 L104 24 L118 40 L74 40 Z" fill="#8c8f93"/>
        <circle cx="44" cy="74" r="14" fill="#fff" stroke="#8c8f93" stroke-width="5"/>
        <circle cx="118" cy="74" r="14" fill="#fff" stroke="#8c8f93" stroke-width="5"/>
      </svg>
      <span class="sector-label">AUTOMOTIVE</span>
    </div>
    <div class="sector">
      <svg viewBox="0 0 160 100" aria-hidden="true">
        <path d="M20 96 L20 50 L50 34 L50 50 L80 34 L80 50 L108 34 L108 8 L128 8 L128 96 Z" fill="#fff"/>
      </svg>
      <span class="sector-label">ENGINEERING</span>
    </div>
  </div>

  <p class="pitch">Our <strong>Capacity</strong> and <strong>Rapid Quenching</strong> drop bottom ovens deliver <strong>precise</strong> processing. We also serve the <strong>leading</strong> names in aerospace, automotive and advanced engineering.</p>

  <div class="contact">
    <div class="contact-item">
      <svg viewBox="0 0 40 40" aria-hidden="true"><circle cx="20" cy="20" r="16" fill="none" stroke="#58595b" stroke-width="4"/><path d="M4 20 H36 M20 4 Q10 20 20 36 Q30 20 20 4" fill="none" stroke="#58595b" stroke-width="3"/></svg>
      <span>www.briskforge.example</span>
    </div>
    <div class="divider"></div>
    <div class="contact-item">
      <svg viewBox="0 0 40 40" aria-hidden="true"><circle cx="20" cy="20" r="17" fill="none" stroke="#58595b" stroke-width="3"/><path d="M14 10 L18 10 L20 16 L17 18 Q19 23 23 24 L25 21 L30 23 L30 27 Q28 30 24 29 Q13 26 11 15 Q11 11 14 10 Z" fill="#58595b"/></svg>
      <span>+44 (0)1632 960418</span>
    </div>
  </div>

  <div class="membership">
    <span class="member-label">Member</span>
    <div class="divider"></div>
    <div class="partner">
      <div class="partner-badge"></div>
      <div class="partner-name">Crafted<br>by the vale</div>
    </div>
  </div>

  <div class="bottom-band"></div>
</div>
</body>
</html>
```